Craft beer label required for new modern craft brewery

I require a label to be designed for my craft beer, the name of the beer is "Lanternfish Pale Ale".
It has to be a contemporary style label targeting an audience group between the ages of 21-40. It must be unique and appealing.
The label must incorporate the image of a Gladiator which has to originally created (I’m giving you creative freedom), not copied (for copy right reasons). I’m attaching a few examples, please refer to “gladiator1.jpg” and “Gladiator2.jpg”.
It would be nice if the Coliseum could appear in the background, also originally created I’m attaching an example, please refer to “Coliseum1.jpg”
The Label must also incorporate the attached logo “Copperwell Brewing Co. Craft Beer-01.jpg” .
The label must fit a 440ml bottle
Please use creative freedom with regards to the shape of the label.
The colours do not have to be exactly the same as logo, but obviously they must match.
Updates

Project Deadline Extended Reason: Not 100% happy with the submissions, almost there.I'd also like to give those designers, that haven't submitted, a chance to submit. Added Tuesday, September 26, 2017

Target Market(s)

Modern/contemporary successful 21-40 year olds

Industry/Entity Type

Brewery

Font styles to use
Serif
Script

Colors

Designer to choose colors to be used in the design.

Requirements
Must have
• My logo, the beer name and the image of a gladiator
• The label size should be at least 10cm wide x 9cm wide.
• The label must include the size of the bottle: 440ml
• The label must include 6.5% ALC./VOL.
Nice to have
• Coliseum in the back ground
Should not have
• Copied images or trade marks

```html
<!DOCTYPE html>
<html lang="en">
<head>
<meta charset="utf-8">
<title>Lanternfish Pale Ale – Label</title>
<link rel="stylesheet" href="https://fonts.googleapis.com/css2?family=Germania+One&display=swap">
<style>
  :root {
    --canvas-bg: #e9e9e7;
    --label-light: #f4f4f3;
    --label-mid: #d9d9d8;
    --label-edge: #bdbdbd;
    --ink: #151515;
    --wood-light: #e9b43a;
    --wood-dark: #c98d1c;
    --badge: #1f2738;
    --badge-text: #f1e4c8;
    --art-light: #e4e0d8;
    --art-mid: #a9a196;
    --art-dark: #6f675c;
    --art-ring: #8e8a84;
  }
  * { margin: 0; padding: 0; box-sizing: border-box; }
  html, body {
    width: 1200px; height: 1200px; overflow: hidden;
    background: var(--canvas-bg);
  }
  .label {
    position: absolute; left: 190px; top: 45px;
    width: 820px; height: 1110px; overflow: hidden;
    background: linear-gradient(90deg, var(--label-edge) 0%, var(--label-light) 12%, var(--label-light) 55%, var(--label-mid) 85%, var(--label-edge) 100%);
    font-family: "Germania One", "Impact", sans-serif;
    color: var(--ink);
  }
  .wood-banner {
    position: absolute; left: 238px; top: 0;
    width: 395px; height: 450px;
    background: linear-gradient(90deg, var(--wood-dark), var(--wood-light) 40%, var(--wood-light) 70%, var(--wood-dark));
  }
  .rule {
    position: absolute; left: 0; width: 100%; height: 11px;
    background: var(--ink);
  }
  .rule--upper { top: 66px; }
  .rule--lower { top: 140px; }
  .brand {
    position: absolute; left: 50%; top: 50px;
    width: 108px; height: 108px; margin-left: -54px;
    border-radius: 50%; background: var(--badge);
    display: flex; align-items: center; justify-content: center;
    text-align: center; padding: 14px;
  }
  .brand__name {
    font-size: 15px; line-height: 1.1; letter-spacing: 1px;
    color: var(--badge-text); text-transform: uppercase;
  }
  .title {
    position: absolute; left: 0; width: 100%;
    text-align: center; text-transform: uppercase; line-height: 1;
    font-weight: 400;
  }
  .title--name { top: 175px; font-size: 112px; }
  .title--style { top: 305px; font-size: 132px; letter-spacing: 10px; }
  .hero-frame {
    position: absolute; left: 150px; top: 470px;
    width: 520px; height: 520px; border-radius: 50%;
    border: 2px solid var(--art-ring);
    padding: 14px;
  }
  .hero-art {
    width: 100%; height: 100%; border-radius: 50%;
    background: radial-gradient(circle at 48% 42%, var(--art-light) 0%, var(--art-mid) 62%, var(--art-dark) 100%);
  }
  .details {
    position: absolute; left: 0; width: 100%; top: 1005px;
    text-align: center; text-transform: uppercase; line-height: 1;
  }
  .details__volume { font-size: 44px; }
  .details__abv { margin-top: 10px; font-size: 30px; letter-spacing: 2px; }
</style>
</head>
<body>
  <main class="label">
    <div class="wood-banner" role="img" aria-label="Golden wooden plank banner"></div>
    <div class="rule rule--upper"></div>
    <div class="rule rule--lower"></div>
    <div class="brand"><span class="brand__name">Copperwell Brewing Co.</span></div>
    <h1 class="title title--name">Lanternfish</h1>
    <h2 class="title title--style">Pale Ale</h2>
    <div class="hero-frame">
      <div class="hero-art" role="img" aria-label="Engraved illustration of a helmeted gladiator with sword and shield in front of the Colosseum"></div>
    </div>
    <div class="details">
      <p class="details__volume">440/ml</p>
      <p class="details__abv">6.5% Alc./Vol.</p>
    </div>
  </main>
</body>
</html>
```